Fin-Tech Firm Captivating Business Card Design

We need a logo design as well to compliment this business card.

We are a new startup based in Singapore called 'Brevora Technologies'.

We develop an array of financial solutions ranging from payment convenience to forex trading and remittance.

Our initial product is Pim - an application which allows user to pre-order food items which would be ready for pickup upon arrival.

We would like to see designs being in black and silver or whatever that looks appealing and exudes a fun and professional feel.

We're not picky as long as it doesn't look like common business cards will do.

I do have a current logo which i do not really like. It will be attached for reference sake

Info:

Brevora Technologies Pte. Ltd.
Company Registration no. 201678213K

FILE TO BE IN .AI and .PSD

Target Market(s)

-F&B (Online-Ordering)
-Finance(P2P Lending and Forex)

Industry/Entity Type

Finance

Contact Information for Business Card

Name
Position
Contact
Email
Address: 47 Merrow Street, Calder House, #14-03 Singapore 068215

Adrian Teo
Founder, Managing Director
+65 98471360
adrian.t@brevoratech.com

Kai Loh
Founder, Executive Director
+65 96603847
kai.l@brevoratech.com

Logo Text

Brevora Technologies

Font styles to use
Sans Serif

Requirements
Must have
• Something that has word play about link brev
• Minimalistic but also something that catches The Eye
• Gold/silver on white/black might be nice
• Animal logo ; horse, eagle, bull or bear
Nice to have
• Just make it look fun and cute
• Just a suggestion to make the Y of brevora stand out
Should not have
• Any landmarks of singapore
• Exclude Pte. Ltd.

```html
<!DOCTYPE html>
<html lang="en">
<head>
<meta charset="utf-8">
<title>Brevora Technologies – Business Card</title>
<link rel="stylesheet" href="https://fonts.googleapis.com/css2?family=Open+Sans:wght@400;600;700&display=swap">
<style>
  :root {
    --backdrop: #3a322d;
    --card: #0d0d0e;
    --card-edge: #1a1a1b;
    --gold: #e8b417;
    --silver: #c9c9cc;
    --white: #f2f2f2;
  }
  * { margin: 0; padding: 0; box-sizing: border-box; }
  html, body {
    width: 1200px; height: 844px; overflow: hidden;
    background: var(--backdrop);
    font-family: "Open Sans", Arial, sans-serif;
  }
  .stage { position: relative; width: 1200px; height: 844px; }
  .card {
    position: absolute;
    width: 520px; height: 300px;
    background: var(--card);
    border: 1px solid var(--card-edge);
    border-radius: 3px;
  }
  .card--front { left: 60px; top: 340px; }
  .card--back  { left: 620px; top: 180px; }

  .brand { position: absolute; display: flex; align-items: center; gap: 14px; }
  .brand__dot {
    width: 70px; height: 70px; border-radius: 50%;
    background: var(--gold);
    flex: none;
  }
  .brand__name {
    color: var(--gold);
    font-size: 26px; font-weight: 600;
    letter-spacing: 1px;
    line-height: 1;
  }
  .card--front .brand { left: 120px; top: 48px; }
  .card--back .brand { left: 128px; top: 115px; }

  .person { position: absolute; left: 34px; top: 176px; color: var(--white); }
  .person__name { color: var(--gold); font-size: 19px; font-weight: 700; line-height: 1.2; }
  .person__role { font-size: 14px; line-height: 1.35; margin-bottom: 8px; }
  .person__address { font-size: 14px; line-height: 1.45; font-style: normal; }

  .contact {
    position: absolute; right: 26px; top: 150px;
    text-align: right; color: var(--white);
    font-size: 13px; line-height: 1.9;
  }
  .contact__line { display: flex; justify-content: flex-end; align-items: center; gap: 5px; }
  .contact__icon { width: 11px; height: 11px; flex: none; }
  .contact__reg { font-weight: 700; font-size: 13.5px; margin-top: 4px; }
</style>
</head>
<body>
<main class="stage">

  <section class="card card--front" aria-label="Business card front">
    <div class="brand">
      <span class="brand__dot"></span>
      <span class="brand__name">Brevora Technologies</span>
    </div>

    <div class="person">
      <p class="person__name">Adrian Teo</p>
      <p class="person__role">Founder, Managing Director</p>
      <address class="person__address">47 Merrow Street, Calder House,<br>#14-03 Singapore 068215</address>
    </div>

    <div class="contact">
      <p class="contact__line">+65 98471360
        <svg class="contact__icon" viewBox="0 0 12 12" aria-hidden="true">
          <path d="M2.5 1 L4.5 1 L5 3.5 L3.8 4.5 Q5 7 7.5 8.2 L8.5 7 L11 7.5 L11 9.5 Q10 11 8.5 11 Q2 9.5 1 3.5 Q1 2 2.5 1Z" fill="var(--gold)"/>
        </svg>
      </p>
      <p class="contact__line">adrian.t@brevoratech.com
        <svg class="contact__icon" viewBox="0 0 12 12" aria-hidden="true">
          <rect x="0.5" y="2" width="11" height="8" fill="var(--gold)"/>
          <path d="M0.5 2 L6 6.5 L11.5 2" fill="none" stroke="var(--card)" stroke-width="1"/>
        </svg>
      </p>
      <p class="contact__reg">Company Registration no. 201678213K</p>
    </div>
  </section>

  <section class="card card--back" aria-label="Business card back">
    <div class="brand">
      <span class="brand__dot"></span>
      <span class="brand__name">Brevora Technologies</span>
    </div>
  </section>

</main>
</body>
</html>
```